Birchline Septic Solutions

Would like to see some single sided ones but would also like to see some double sided with one sided only being the logo. Owners name is Colin Vandro. Phone number is 555-214-0387
Services are pumping, inspections, installs, and repairs

Contact Information for Business Card

555-241-0387 Colin Vandro Fernwick, OH

```html
<!DOCTYPE html>
<html lang="en">
<head>
<meta charset="utf-8">
<title>Birchline Septic Solutions – Business Card</title>
<link rel="stylesheet" href="https://fonts.googleapis.com/css2?family=Montserrat:wght@500;600;700;800&display=swap">
<style>
  :root {
    --backdrop: #9b9b9b;
    --paper: #ffffff;
    --ink: #0d0d0d;
    --teal: #2ebdba;
    --night: #000000;
    --night-soft: #1b1b1b;
    --rule: #b5b5b5;
  }
  * { box-sizing: border-box; margin: 0; padding: 0; }
  html, body {
    width: 1093px;
    height: 1200px;
    overflow: hidden;
    background: var(--backdrop);
    font-family: "Montserrat", sans-serif;
  }
  .card {
    position: absolute;
    left: 264px;
    width: 580px;
    height: 357px;
    border-radius: 30px;
    overflow: hidden;
  }
  /* Front */
  .card--front { top: 226px; background: var(--paper); color: var(--ink); }
  .brand {
    position: absolute;
    left: 30px;
    top: 172px;
    width: 255px;
    text-align: center;
    font-weight: 800;
    color: var(--ink);
    line-height: 1.05;
  }
  .brand__name { display: block; font-size: 35px; letter-spacing: 0.5px; }
  .brand__tag { display: block; font-size: 12.5px; letter-spacing: 4.6px; margin-top: 14px; }
  .divider {
    position: absolute;
    left: 289px;
    top: 100px;
    width: 1px;
    height: 157px;
    background: var(--rule);
  }
  .contact { position: absolute; left: 312px; top: 121px; }
  .contact__name { font-size: 22px; font-weight: 700; letter-spacing: 0.3px; text-transform: uppercase; }
  .contact__list { list-style: none; margin-top: 30px; }
  .contact__item {
    display: flex;
    align-items: center;
    gap: 8px;
    font-size: 16.5px;
    font-weight: 500;
    letter-spacing: 0.4px;
    height: 26px;
  }
  .contact__icon { width: 16px; height: 18px; flex: none; }
  .services {
    position: absolute;
    left: 0;
    top: 291px;
    width: 100%;
    height: 35px;
    background: var(--teal);
    color: var(--paper);
    font-size: 17px;
    font-weight: 600;
    letter-spacing: 0.2px;
    display: flex;
    align-items: center;
    justify-content: center;
    gap: 8px;
  }
  .services__dot { width: 7px; height: 7px; border-radius: 50%; background: var(--paper); }
  /* Back */
  .card--back { top: 621px; background: var(--night); }
  .scenery {
    position: absolute;
    inset: 0;
    background:
      radial-gradient(ellipse 70% 85% at 85% 80%, var(--night-soft) 0%, var(--night-soft) 45%, transparent 70%),
      linear-gradient(180deg, transparent 50%, #111 100%);
  }
  .brand--back {
    left: 0;
    top: 160px;
    width: 100%;
    color: var(--paper);
  }
  .brand--back .brand__name { font-size: 60px; }
  .brand--back .brand__tag { font-size: 21px; letter-spacing: 7.5px; margin-top: 22px; }
</style>
</head>
<body>
  <section class="card card--front" aria-label="Business card front">
    <div class="brand">
      <span class="brand__name">BIRCHLINE</span>
      <span class="brand__tag">SEPTIC SOLUTIONS</span>
    </div>
    <div class="divider"></div>
    <div class="contact">
      <h1 class="contact__name">Colin Vandro</h1>
      <ul class="contact__list">
        <li class="contact__item">
          <svg class="contact__icon" viewBox="0 0 24 24" aria-hidden="true">
            <path d="M6.6 10.8a15.1 15.1 0 0 0 6.6 6.6l2.2-2.2a1 1 0 0 1 1-.25 11.4 11.4 0 0 0 3.6.6 1 1 0 0 1 1 1V20a1 1 0 0 1-1 1A17 17 0 0 1 3 4a1 1 0 0 1 1-1h3.5a1 1 0 0 1 1 1c0 1.250.2 2.45.6 3.6a1 1 0 0 1-.25 1z" fill="none" stroke="var(--teal)" stroke-width="2"/>
            <path d="M14 3a7 7 0 0 1 7 7M14 7a3 3 0 0 1 3 3" fill="none" stroke="var(--teal)" stroke-width="2" stroke-linecap="round"/>
          </svg>
          555-214-0387
        </li>
        <li class="contact__item">
          <svg class="contact__icon" viewBox="0 0 24 28" aria-hidden="true">
            <path d="M12 1a10 10 0 0 0-10 10c0 7 10 16 10 16s10-9 10-16A10 10 0 0 0 12 1z" fill="var(--teal)"/>
            <circle cx="12" cy="11" r="3.6" fill="var(--paper)"/>
          </svg>
          Fernwick, OH
        </li>
      </ul>
    </div>
    <div class="services">
      <span>PUMPING</span><span class="services__dot"></span>
      <span>INSPECTIONS</span><span class="services__dot"></span>
      <span>INSTALLS</span><span class="services__dot"></span>
      <span>REPAIRS</span>
    </div>
  </section>

  <section class="card card--back" aria-label="Business card back">
    <div class="scenery" role="img" aria-label="Faint dark silhouette of mountains and pine forest"></div>
    <div class="brand brand--back">
      <span class="brand__name">BIRCHLINE</span>
      <span class="brand__tag">SEPTIC SOLUTIONS</span>
    </div>
  </section>
</body>
</html>
```